New florist business website design

Number 1 want is an easy to navigate & check out website
Needs to be beautiful and eye catching as well.
This is an online only business (no shop front)
Rustic and blush pinks, neutrals, woods, leaves
Customers need to be able to go onto my website, select something they want to buy but have the option to use a drop down box to change colours of the flowers, or add notes to make changes to the arrangement

Industry/Entity Type

Florist

Coding

Coded - Design and coding required

Number of Pages Required

5+ page

Colors
f9d9e8
fff2ec
fffefc

Requirements
Must have
• Drop down menu to take you to other pages for Arrangements, bouquets, everlasting arrangements, gifts, contact
Be able to purchase and “add to basket”
Checkout page
Nice to have
• Be able to add my own photos once I’ve taken new ones
Should not have
• Tacky images or clip art

```html
<!DOCTYPE html>
<html lang="en">
<head>
<meta charset="utf-8">
<title>Rose &amp; Reed — Florist</title>
<link href="https://fonts.googleapis.com/css2?family=Josefin+Sans:wght@300;400&family=Great+Vibes&family=Lora:ital@0;1&display=swap" rel="stylesheet">
<style>
:root{
  --blush:#f9d9e8;
  --peach:#fff2ec;
  --cream:#fffefc;
  --rose:#f08aa6;
  --ink:#1d1d1d;
  --muted:#6b6b6b;
  --grey-band:#f3f3f3;
  --frame:#d9d9d9;
}
*{margin:0;padding:0;box-sizing:border-box}
html,body{width:1200px;height:4777px;overflow:hidden;background:var(--cream)}
body{position:relative;font-family:'Josefin Sans',sans-serif;color:var(--ink)}
.abs{position:absolute}
.script{font-family:'Great Vibes',cursive;font-weight:400;color:var(--ink)}
.serif{font-family:'Lora',serif}
.heading{font-weight:400;letter-spacing:1px;text-transform:uppercase}
.rule{position:absolute;height:2px;width:48px;background:var(--rose);left:576px}
.center{left:0;width:1200px;text-align:center}
.btn{position:absolute;display:flex;align-items:center;justify-content:center;font-size:15px;text-transform:uppercase;letter-spacing:.5px;font-family:'Lora',serif}
.btn-solid{background:var(--rose);color:#fff}
.btn-outline{border:2px solid var(--rose);color:var(--ink);background:transparent}
.photo{position:absolute}

.logo{position:absolute;left:150px;top:62px;display:flex;align-items:center;gap:12px;font-size:34px;font-weight:300}
.logo .dot{width:14px;height:14px;border-radius:50%;background:var(--rose)}
.nav{position:absolute;top:82px;left:440px;font-family:'Lora',serif;font-size:15px}
.nav a{color:var(--ink);text-decoration:none;position:absolute;white-space:nowrap}
.nav .active::after{content:"";position:absolute;left:0;right:0;bottom:-8px;height:2px;background:var(--rose)}
.phone{position:absolute;left:800px;top:22px;display:flex;align-items:center;gap:14px;font-size:21px;font-weight:300}

.card{position:absolute;width:253px;height:198px;border:2px solid var(--frame);background:#fff}
.card .photo{left:12px;top:12px;width:225px;height:170px}
.tag{position:absolute;top:8px;right:8px;background:#111;color:#fff;font-size:9px;padding:2px 5px;z-index:1}
.pname{position:absolute;width:253px;text-align:center;font-size:16px;color:var(--muted)}
.price{position:absolute;width:253px;text-align:center;font-size:15px;color:var(--rose);font-family:'Lora',serif}

.promo{position:absolute;overflow:hidden}
.promo .off{position:absolute;color:var(--rose);font-size:28px;font-weight:300}
.promo .title{position:absolute;font-size:38px;line-height:1.2;text-transform:uppercase}

.partner{position:absolute;top:2560px;height:56px;border-radius:6px;background:#e6e3e3}

.quote{position:absolute;left:241px;top:3106px;width:718px;text-align:center;font-family:'Lora',serif;font-style:italic;font-size:15px;line-height:26px;color:var(--muted)}

.insta{position:absolute;width:220px;height:200px}

.foot-nav{position:absolute;top:4598px;font-size:16px;text-transform:uppercase;font-weight:300}
.card-pay{position:absolute;top:4530px;width:44px;height:28px;border-radius:4px}
.social{position:absolute;top:4700px;width:24px;height:24px;border-radius:50%;background:var(--ink)}
</style>
</head>
<body>

<!-- hero -->
<svg class="abs" style="left:0;top:0" width="1200" height="820" viewBox="0 0 1200 820" aria-hidden="true">
  <defs>
    <linearGradient id="heroBg" x1="0" y1="0" x2="1" y2="0">
      <stop offset="0" stop-color="#fbe4ed"/>
      <stop offset="1" stop-color="#f7d0de"/>
    </linearGradient>
  </defs>
  <path d="M0 0H1200V780C1150 800 1110 760 1060 790C1000 810 950 760 880 790C820 805 760 770 700 790C620 805 560 760 480 785C400 800 340 770 260 790C190 800 120 770 60 790C30 795 10 780 0 775Z" fill="url(#heroBg)"/>
</svg>
<div class="photo" role="img" aria-label="Pink tulip bouquet wrapped in pink paper" style="left:760px;top:150px;width:400px;height:560px;border-radius:8px;background:linear-gradient(160deg,#f6c3d4,#ee9fba)"></div>

<div class="logo"><span class="dot"></span>Rose &amp; Reed</div>
<div class="phone">
  <svg width="34" height="34" viewBox="0 0 34 34" aria-hidden="true"><circle cx="17" cy="17" r="15.5" fill="none" stroke="#1d1d1d" stroke-width="2"/><path d="M11 9c1-1 2.5-1 3 0l2 3c.5 1 0 2-1 2.5l-1 .6c1 2.5 3 4.5 5.5 5.5l.6-1c.5-1 1.5-1.5 2.5-1l3 2c1 .5 1 2 0 3l-1.5 1.5C20 26 8 14 9.5 10.5Z" fill="#1d1d1d"/></svg>
  <span>Call : 1 800 555 0142</span>
</div>
<nav class="nav">
  <a class="active" style="left:0">Home</a>
  <a style="left:76px">Shop Products</a>
  <a style="left:210px">About Us</a>
  <a style="left:311px">Blog</a>
  <a style="left:378px">Contact</a>
</nav>
<svg class="abs" style="left:908px;top:82px" width="20" height="20" viewBox="0 0 20 20" aria-label="Search"><circle cx="8" cy="8" r="6" fill="none" stroke="#1d1d1d" stroke-width="2"/><path d="M12.5 12.5L18 18" stroke="#1d1d1d" stroke-width="2"/></svg>
<svg class="abs" style="left:963px;top:82px" width="20" height="20" viewBox="0 0 20 20" aria-label="Account"><circle cx="10" cy="6" r="4.5" fill="none" stroke="#1d1d1d" stroke-width="1.8"/><path d="M2 19c1-5 4-7 8-7s7 2 8 7" fill="none" stroke="#1d1d1d" stroke-width="1.8"/></svg>
<svg class="abs" style="left:1028px;top:78px" width="28" height="26" viewBox="0 0 28 26" aria-label="Basket"><path d="M3 9h16l-1.5 14h-13Z" fill="none" stroke="#1d1d1d" stroke-width="1.8"/><path d="M7 9V6a4 4 0 0 1 8 0v3" fill="none" stroke="#1d1d1d" stroke-width="1.8"/><circle cx="21" cy="6" r="6" fill="#1d1d1d"/><text x="21" y="9" font-size="8" fill="#fff" text-anchor="middle" font-family="Josefin Sans">0</text></svg>

<div class="abs script" style="left:145px;top:282px;font-size:64px">New Collections</div>
<h1 class="abs heading" style="left:147px;top:382px;font-size:58px">A Perpect Bouquet</h1>
<div class="btn btn-solid" style="left:147px;top:495px;width:161px;height:52px">Shop Now</div>
<div class="btn btn-outline" style="left:322px;top:495px;width:162px;height:52px">Add to Basket</div>
<svg class="abs" style="left:144px;top:628px" width="50" height="12" aria-hidden="true"><circle cx="6" cy="6" r="3.5" fill="none" stroke="#1d1d1d"/><circle cx="18" cy="6" r="4" fill="#1d1d1d"/><circle cx="30" cy="6" r="3.5" fill="none" stroke="#1d1d1d"/><circle cx="42" cy="6" r="3.5" fill="none" stroke="#1d1d1d"/></svg>

<!-- featured -->
<div class="abs script center" style="top:852px;font-size:52px">Shop By</div>
<h2 class="abs heading center" style="top:940px;font-size:44px">Featured Collection</h2>
<div class="rule" style="top:1010px"></div>

<svg class="abs" style="left:46px;top:1122px" width="428" height="510" viewBox="0 0 428 510" aria-hidden="true">
  <path d="M150 20C210 0 260 30 300 60C350 70 370 120 360 170C400 200 428 250 400 300C420 350 390 400 350 420C330 470 280 500 220 480C170 510 120 490 100 450C50 450 20 400 40 350C0 310 10 250 50 220C40 170 60 110 100 90C110 50 130 30 150 20Z" fill="var(--blush)"/>
</svg>
<div class="abs script" style="left:46px;width:428px;text-align:center;top:1272px;font-size:36px">Summer</div>
<div class="abs" style="left:46px;width:428px;text-align:center;top:1336px;font-size:60px">SALE 10%</div>
<div class="btn btn-solid" style="left:180px;top:1434px;width:161px;height:50px">Shop Now</div>

<div class="card" style="left:534px;top:1100px"><div class="photo" role="img" aria-label="Bouquet of red, orange and yellow roses" style="background:linear-gradient(160deg,#f3b04a,#dc4a36)"></div></div>
<div class="card" style="left:803px;top:1100px"><div class="tag">SALE</div><div class="photo" role="img" aria-label="Christmas wreath with red flowers" style="background:linear-gradient(160deg,#6b8f55,#b8323b)"></div></div>
<div class="pname" style="left:534px;top:1326px">PRODUCT NAME</div>
<div class="price" style="left:534px;top:1358px">$207.2</div>
<div class="pname" style="left:803px;top:1326px">PRODUCT NAME</div>
<div class="price" style="left:803px;top:1358px">$207.2</div>

<div class="card" style="left:534px;top:1397px"><div class="tag">SALE</div><div class="photo" role="img" aria-label="Dried flowers in a mauve vase" style="background:linear-gradient(180deg,#dcc6a6,#9c8088)"></div></div>
<div class="card" style="left:803px;top:1397px"><div class="photo" role="img" aria-label="Mixed bouquet of purple and red flowers" style="background:linear-gradient(160deg,#8d63c0,#d9473f)"></div></div>
<div class="pname" style="left:534px;top:1623px">PRODUCT NAME</div>
<div class="price" style="left:534px;top:1655px">$207.2</div>
<div class="pname" style="left:803px;top:1623px">PRODUCT NAME</div>
<div class="price" style="left:803px;top:1655px">$207.2</div>

<!-- promos -->
<div class="promo" role="img" aria-label="Everlasting pink rose under a glass dome" style="left:145px;top:1796px;width:541px;height:343px;background:linear-gradient(180deg,#fdeee8 0%,#f6ddd6 55%,#e8c3c3 100%)">
  <div class="off" style="left:36px;top:40px">-30%OFF</div>
  <div class="title" style="left:192px;top:40px">Everlasting<br>Arrangements</div>
</div>
<div class="promo" role="img" aria-label="Pink rose bouquet" style="left:694px;top:1796px;width:361px;height:343px;background:linear-gradient(180deg,#f4cadd 0%,#efb5cd 100%)">
  <div class="off" style="left:140px;top:218px">20%OFF</div>
  <div class="title" style="left:140px;top:272px">Bouquets</div>
</div>
<div class="promo" role="img" aria-label="Red roses and gift box" style="left:145px;top:2146px;width:360px;height:343px;background:linear-gradient(180deg,#f6ead6 0%,#ead4b6 55%,#c9868a 100%)">
  <div class="off" style="left:126px;top:50px">20%OFF</div>
  <div class="title" style="left:130px;top:108px">Gifts</div>
</div>
<div class="promo" role="img" aria-label="Protea and native flower arrangement in a white vase" style="left:514px;top:2146px;width:541px;height:343px;background:linear-gradient(90deg,#e4eef8 0%,#e4eef8 45%,#d8c9cf 100%)">
  <div class="off" style="left:54px;top:194px">-30%OFF</div>
  <div class="title" style="left:54px;top:248px">Arrangements</div>
</div>

<!-- partners -->
<div class="partner" style="left:52px;width:110px;border-radius:50%;height:80px;top:2548px"></div>
<div class="partner" style="left:232px;width:134px"></div>
<div class="partner" style="left:420px;width:100px"></div>
<div class="partner" style="left:600px;width:96px"></div>
<div class="partner" style="left:748px;width:188px"></div>
<div class="partner" style="left:1004px;width:152px"></div>

<!-- testimonials -->
<svg class="abs" style="left:0;top:2660px" width="1200" height="750" viewBox="0 0 1200 750" aria-hidden="true">
  <path d="M0 60C60 40 100 80 160 60C240 30 300 70 380 50C460 30 520 70 600 50C700 20 760 60 840 40C920 10 980 50 1060 30C1120 20 1160 40 1200 30V700C1140 720 1100 690 1040 710C960 730 900 690 820 710C740 730 680 700 600 715C520 730 460 695 380 712C300 728 240 700 160 715C100 725 50 705 0 715Z" fill="var(--grey-band)"/>
</svg>
<div class="photo" role="img" aria-label="Hanging basket of pink flowers" style="left:12px;top:2840px;width:120px;height:120px;border-radius:8px;background:linear-gradient(160deg,#e3c6d6,#b7c9ab)"></div>
<div class="photo" role="img" aria-label="Purple and pink bouquet" style="left:830px;top:2720px;width:186px;height:170px;border-radius:8px;background:linear-gradient(160deg,#d9a6c4,#9e7bb0)"></div>
<div class="abs script center" style="top:2890px;font-size:44px">Reviews</div>
<h2 class="abs heading center" style="top:2972px;font-size:44px">Client Testimonials</h2>
<div class="rule" style="top:3040px"></div>
<svg class="abs" style="left:148px;top:3124px" width="34" height="64" aria-label="Previous"><path d="M32 2L2 32L32 62" fill="none" stroke="#aaa" stroke-width="1.5"/></svg>
<svg class="abs" style="left:1020px;top:3124px" width="34" height="64" aria-label="Next"><path d="M2 2L32 32L2 62" fill="none" stroke="#aaa" stroke-width="1.5"/></svg>
<p class="quote">"Lorem ipsum dolor sit amet, consectetur adipiscing edo eiusmod tempor incididunt ut labore et dolore magna aliqua ipsum suspendisse ultrices gravs commoverra maecenas accumsan lacus vel facilisiem ipsum dolor sit amet, consectetur adipiscing edo eiusmod tempor incididunt ut labore et dolore magna aliqua ipsum suspendisse ultrices gravida maecenas accumsan lacus vel facilisis"</p>
<div class="photo" role="img" aria-label="Customer portrait" style="left:491px;top:3235px;width:78px;height:78px;border-radius:50%;background:linear-gradient(#d6c8bb,#ece4dd)"></div>
<div class="abs serif" style="left:590px;top:3252px;font-size:16px">CLARA WELLS</div>
<div class="abs serif" style="left:590px;top:3278px;font-size:14px;color:var(--muted);font-style:italic">Customer</div>
<div class="photo" role="img" aria-label="Red flowering plant in a wooden planter" style="left:624px;top:3345px;width:180px;height:180px;border-radius:8px;background:linear-gradient(180deg,#d7b0b4,#c8a98a)"></div>

<!-- instagram -->
<div class="abs script center" style="top:3600px;font-size:50px">Follow Us</div>
<h2 class="abs heading center" style="top:3680px;font-size:44px">Instagram</h2>
<div class="rule" style="top:3754px"></div>
<div class="insta" role="img" aria-label="Pressed flower cards on wood" style="left:145px;top:3810px;background:linear-gradient(135deg,#ebe5dd,#c3b3dc)"></div>
<div class="insta" role="img" aria-label="Bouquet held against pink wall" style="left:375px;top:3810px;background:linear-gradient(135deg,#ec8fae,#e06b93)"></div>
<div class="insta" role="img" aria-label="Two women sharing a gift at home" style="left:605px;top:3810px;background:linear-gradient(135deg,#d6d2c9,#ece7e1)"></div>
<div class="insta" role="img" aria-label="Woman holding a rose under glass" style="left:835px;top:3810px;background:linear-gradient(135deg,#cfa7a3,#8b2a35)"></div>
<div class="insta" role="img" aria-label="Daisies in a metal pot outdoors" style="left:145px;top:4020px;background:linear-gradient(180deg,#ece3a2,#6f8c52)"></div>
<div class="insta" role="img" aria-label="Pink gerberas and roses" style="left:375px;top:4020px;background:linear-gradient(135deg,#e35c85,#9a3446)"></div>
<div class="insta" role="img" aria-label="Dark red roses with a white frame" style="left:605px;top:4020px;background:linear-gradient(135deg,#9e1f40,#4e1020)"></div>
<div class="insta" role="img" aria-label="Pink roses wrapped in kraft paper" style="left:835px;top:4020px;background:linear-gradient(180deg,#f1efed,#d0a98a)"></div>
<div class="btn btn-solid" style="left:519px;top:4272px;width:162px;height:50px">Load More</div>

<!-- footer -->
<svg class="abs" style="left:0;top:4400px" width="1200" height="377" viewBox="0 0 1200 377" aria-hidden="true">
  <path d="M0 30C80 10 140 50 220 30C320 5 380 45 480 25C580 5 640 40 740 20C840 0 900 35 1000 18C1080 5 1140 30 1200 20V377H0Z" fill="var(--peach)"/>
</svg>
<div class="card-pay" style="left:145px;background:#d8dbe8"></div>
<div class="card-pay" style="left:202px;background:#efc9b3"></div>
<div class="card-pay" style="left:259px;background:#e5e0d8"></div>
<div class="card-pay" style="left:316px;background:#9fb6d8"></div>
<div class="card-pay" style="left:373px;background:#d7e1ec"></div>
<div class="foot-nav" style="left:143px">Home</div>
<div class="foot-nav" style="left:234px">Shop Products</div>
<div class="foot-nav" style="left:408px">About Us</div>
<div class="foot-nav" style="left:532px">Blog</div>
<div class="foot-nav" style="left:614px">Contact</div>
<div class="abs serif" style="left:143px;top:4646px;font-size:12px;color:#444">Copyright 2021 Rose &amp; Reed All Rights Reserved &nbsp;|&nbsp; Privacy Policy &nbsp;|&nbsp; Terms</div>
<div class="social" style="left:140px"></div>
<div class="social" style="left:192px"></div>
<div class="social" style="left:250px"></div>
<div class="abs" style="left:790px;top:4590px;display:flex;align-items:center;gap:12px;font-size:40px;font-weight:300"><span style="width:14px;height:14px;border-radius:50%;background:var(--rose)"></span>Rose &amp; Reed</div>

</body>
</html>
```